A unique communication angle to crowdfunding

Looking for a fresh redesign of a crowd funding website that deals in real estate. I already have the content, but am looking to take the design to the next level.

Existing real estate crowd funding sites focus on the real estate. I want to explore communication angle that:
- puts the investor in the centre of the communication: "become a baron"
- highlights the international nature (international properties, international investors)

There's also quite a lot of copy on the site, as we need to explain the service in quite a bit of detail. There's room to reduce the copy and replace with graphics. Could also consider clicking to see different text (see our difference section in http://galleonfairs.com)

The backend of the platform is already being worked on by a specialist crowd funding service provider.

In total there are 5 pages to be designed.

The homepage is really important. Right now it looks quite dated. It doesn't have a great layout. Note there is no mobile version of the website, so the pages need to be seen well on mobile devices. When looking at the brief, refer to the following links too:

current website:
http://pennyduke.com

some revisions made so far:
http://preview.stakeharbor.com/7K3LQ9

Attached are logo files and another file which contained copy for the pages. No need to rework the logo.

Please make sure to use the same copy in the brief on the webpages, to ensure the layouts work. Designers are free to propose images they feel work on the pages.

I would like to see if rather than tweaking the pages, it's possible to come up with a better design concept. If the 5 pages are accepted, there's a chance I'll request an additional 4 pages.
Updates

Please note the font used in the logo is called "harabara" in case you decide to use it in any of the titles, etc.

Please note there is one additional page for which we would like to review designs. Note the page would be a template to be used on all future real estate detail pages. Here is an example of the current design for reference:

http://pennyduke.com/projects/view/14

In total there are 5 page designs required, (homepage + 4)

Thank you

FYI -

Just a quick note to give information from similar UK real estate crowdfunding sites:
http://www.housewalrus.co.uk
http://tiderock.co.uk
https://www.fundquarry.com

Of the above, only tiderock has a nice clean looking landing page. Information is clear and well laid out.

Hi all, just uploaded a new file in the brief. Contains some comments and a website reference. I thought it may help to explain how we could convey international aspect as well as how we could convey images in a more modern way. This is an option you can consider, but its entirely up to you how how answer the brief. Thanks!

Reason: As requested by some designers needing more time to complete their work. Continue to share your work in progress and receive timely feedback before the deadline.

We would like to let you know that we have just shortlisted the best designs. Together with that, we have also passed some detailed feedback to all designers who weren't shortlisted. If we didn't contact you, please let us know. If you haven't submitted a design or are working on revisions, please note these will no longer be taken into account now. We hope you understand that we need to close the project today. Thank you all once again for your great work and design concepts. Here's hoping we meet again on a future design brief. Cheers, pennyduke team.

Target Market(s)

At the moment, only rich are able to buy real estate. With this service, anyone can become a landlord. Target buyers:

Young professionals, looking to diversify from stock market and lower risk
People nearing retirement, looking for stable rental incomes
Retirees - looking to supplement pensions with possibility of capital gains
Parents - looking for a way to save long term for their children (instead of low interest paying bank accounts)

Industry/Entity Type

Communication

Font styles to use
Sans Serif
Other font styles liked:
• harabara

Colors
add136
f5f9eb
959595
000000

Requirements
Must have
• Overall, the site must convey "whoever you are, you too can become a landlord", and that you don't need to be wealthy to invest in real estate. See

Communication should put the investor (or the baron) at the centre. The investor can be any of those described in the target market.

Show the aspirational side of property ownership.

In addition to the investor/baron character, the second main theme is international. No other real estate crowdfunding website highlights this.
Nice to have
• Banner could show different consumer types, to illustrate that the service can appeal to many different profiles. Refer to attached file "home page reference - plainasbread.com" as an example of how this could be done.

Aim to show the international side of the service. Properties around the world, investors around the world.

```html
<!DOCTYPE html>
<html lang="en">
<head>
<meta charset="utf-8">
<title>pennyduke – Build your property portfolio</title>
<link rel="stylesheet" href="https://fonts.googleapis.com/css2?family=Open+Sans:wght@400;600;700;800&display=swap">
<style>
:root{
  --green:#add136;
  --green-dark:#8fb21e;
  --pale:#f5f9eb;
  --grey:#959595;
  --grey-light:#e4e4e4;
  --pink:#e8336b;
  --black:#000;
  --ink:#333;
  --white:#fff;
}
*{box-sizing:border-box;margin:0;padding:0}
html,body{width:1200px;height:4000px;overflow:hidden;background:var(--white)}
body{font-family:"Open Sans",Arial,sans-serif;color:var(--ink);position:relative}
.page{position:relative;width:1200px;height:4000px}

/* header + hero */
.hero{position:absolute;top:0;left:0;width:1200px;height:900px;
  background:linear-gradient(180deg,#dfe6d8 0%,#b9c6a8 35%,#7f8b63 60%,#4a4730 85%,#2f2b1f 100%)}
.hero-photo{position:absolute;inset:0}
.site-header{position:absolute;top:0;left:0;width:1200px;height:110px;display:flex;align-items:center;padding:0 40px;z-index:2}
.brand{display:flex;align-items:center;gap:12px;font-family:"Open Sans",sans-serif;font-weight:600;font-size:34px;color:var(--green-dark)}
.brand-dot{width:40px;height:40px;border-radius:50%;background:var(--green)}
.main-nav{display:flex;gap:26px;margin-left:44px;font-size:17px;font-weight:600;color:var(--black);text-transform:uppercase}
.social{position:absolute;right:40px;top:22px;display:flex;gap:12px}
.social span{width:34px;height:34px;border-radius:50%;border:2px solid var(--ink)}
.hero-copy{position:absolute;top:560px;width:1200px;text-align:center;color:var(--white)}
.hero-title{font-size:44px;font-weight:800;letter-spacing:1px}
.hero-sub{font-size:40px;font-weight:400;letter-spacing:3px;margin-top:6px}
.hero-down{position:absolute;top:690px;left:555px}
.hero-dots{position:absolute;top:848px;left:560px;display:flex;gap:14px}
.hero-dots span{width:18px;height:18px;border-radius:50%;background:rgba(255,255,255,.6)}
.hero-dots span:first-child{background:var(--white)}

/* intro band */
.intro{position:absolute;top:900px;left:0;width:1200px;height:250px;background:var(--green);color:var(--white);text-align:center;padding-top:28px}
.intro h2{font-size:25px;font-weight:700;margin:12px 0 6px}
.intro p{font-size:20px;line-height:1.3;width:960px;margin:0 auto}

/* actions */
.actions{position:absolute;top:1150px;left:0;width:1200px;height:330px;background:var(--pale);border-bottom:1px solid var(--grey-light)}
.action{position:absolute;top:100px;display:flex;gap:30px;width:480px}
.action-tile{flex:0 0 140px;width:140px;height:135px;background:var(--grey);color:var(--white);display:flex;flex-direction:column;align-items:center;justify-content:flex-end;padding-bottom:14px;font-size:14px;text-align:center;text-transform:uppercase;line-height:1.2}
.action-tile svg{margin-bottom:14px}
.action h3{font-size:30px;font-weight:600;color:var(--grey)}
.action p{font-size:19px;color:var(--grey);line-height:1.25;margin-top:4px}

/* section titles */
.section-title{position:absolute;left:0;width:1200px;text-align:center;color:var(--green);font-size:30px;font-weight:700}
.section-rule{position:absolute;left:90px;width:1020px;height:2px;background:var(--green)}
.section-lead{position:absolute;left:0;width:1200px;text-align:center;color:var(--grey);font-size:20px;line-height:1.3}
.section-lead strong{color:var(--green-dark)}

/* projects */
.project{position:absolute;top:1635px;width:330px;height:380px;background:var(--pale);border:1px solid var(--grey-light)}
.project-photo{height:140px;background:linear-gradient(160deg,#3b4b6b,#17213a 70%,#0e1322);position:relative}
.project-badge{position:absolute;left:12px;top:18px;background:#2a5ba8;color:var(--white);font-size:12px;padding:3px 10px}
.project-price{position:absolute;right:0;top:0;background:var(--green);color:var(--white);font-size:15px;font-weight:700;padding:10px 14px}
.project-body{padding:12px 14px}
.project-name{color:var(--green-dark);font-size:15px;font-weight:700}
.project-desc{font-size:12px;line-height:1.35;color:var(--ink);margin-top:6px;height:70px}
.project-bar{height:14px;background:var(--white);border:1px solid var(--grey-light);margin-top:14px}
.project-bar span{display:block;height:100%;background:var(--green)}
.project-funded{font-size:13px;margin-top:8px;padding-bottom:12px;border-bottom:1px solid var(--grey-light)}
.project-link{font-size:14px;color:var(--green-dark);font-weight:600;margin-top:12px}

/* community */
.banner{position:absolute;left:90px;width:1020px;height:44px;background:var(--green);color:var(--white);font-size:19px;text-align:center;line-height:44px;white-space:nowrap}
.world-map{position:absolute;top:2240px;left:90px;width:1020px;height:490px;background:radial-gradient(ellipse at 50% 45%,#d4d4d4 0%,#eaeaea 70%,#fafafa 100%)}
.legend{position:absolute;left:90px;font-size:18px;color:var(--grey);display:flex;align-items:center;gap:16px}
.legend i{width:34px;height:34px;display:block}

/* donut */
.donut{position:absolute;top:2905px;left:370px}
.donut-label{position:absolute;font-size:20px;color:var(--ink)}
.donut-note{position:absolute;top:3395px;left:370px;width:460px;font-size:16px;color:var(--grey);line-height:1.3}

/* press */
.press{position:absolute;top:3465px;left:0;width:1200px;height:165px;background:var(--white);border-top:1px solid var(--grey-light)}
.press-label{position:absolute;left:90px;top:14px;font-size:14px;color:var(--ink)}
.press-badge{position:absolute;height:40px;background:#bdbdbd}

/* footer */
.site-footer{position:absolute;top:3630px;left:0;width:1200px;height:320px;background:var(--black);color:#cfcfcf;padding:20px 90px;font-size:11.5px;line-height:1.4}
.footer-brand{position:absolute;right:90px;top:30px;font-family:"Open Sans",sans-serif;font-weight:600;font-size:30px;color:var(--white);line-height:1}
.site-footer p{width:1020px;margin-bottom:12px}
.site-footer p.lead{width:620px;font-size:13px;margin-bottom:40px}
.copyright{position:absolute;top:3950px;left:0;width:1200px;height:50px;background:#5a5a5a;color:var(--white);font-size:16px;display:flex;align-items:center;justify-content:center;gap:12px}
.copyright span.circle{width:24px;height:24px;border-radius:50%;border:2px solid var(--white)}
</style>
</head>
<body>
<div class="page">

  <section class="hero">
    <div class="hero-photo" role="img" aria-label="Photo of small green model houses standing on stacks of coins"></div>
    <header class="site-header">
      <div class="brand"><span class="brand-dot"></span>pennyduke</div>
      <nav class="main-nav">
        <span>Home</span><span>Sign in</span><span>How it works</span><span>Discover a project</span><span>The Baron blog</span><span>FAQs</span>
      </nav>
      <div class="social"><span></span><span></span></div>
    </header>
    <div class="hero-copy">
      <h1 class="hero-title">BUILD YOUR PROPERTY PORTFOLIO</h1>
      <p class="hero-sub">POOL WIYH FRIENDS. SHARE THE GAINS</p>
    </div>
    <svg class="hero-down" width="90" height="90" viewBox="0 0 90 90" aria-hidden="true">
      <circle cx="45" cy="45" r="40" fill="none" stroke="#fff" stroke-width="5"/>
      <path d="M28 38 L45 55 L62 38" fill="none" stroke="#fff" stroke-width="6" stroke-linecap="round" stroke-linejoin="round"/>
    </svg>
    <div class="hero-dots"><span></span><span></span><span></span></div>
  </section>

  <section class="intro">
    <svg width="60" height="60" viewBox="0 0 60 60" aria-hidden="true">
      <path d="M12 48 L42 18 M18 12 L48 42" stroke="#fff" stroke-width="7" stroke-linecap="round"/>
      <circle cx="44" cy="14" r="8" fill="none" stroke="#fff" stroke-width="5"/>
    </svg>
    <h2>Reconstructing a property ladder that's strong and fair</h2>
    <p>By harnessing the power of crowds, it's possible to become a landlord in locations around the world. Forget the burden of financing 100% of the purchase. Leave the day to day management of your property portfolio to us. Start with 1% in a project and plan your steps to becoming a true baron.</p>
  </section>

  <section class="actions">
    <div class="action" style="left:90px">
      <div class="action-tile">
        <svg width="54" height="54" viewBox="0 0 54 54" aria-hidden="true"><circle cx="27" cy="27" r="24" fill="none" stroke="#fff" stroke-width="4"/><path d="M23 16 L34 27 L23 38" fill="none" stroke="#fff" stroke-width="4"/></svg>
        Sign up<br>to buy
      </div>
      <div><h3>Find properties</h3><p>Sign up to browse the portfolio. Your journey to becoming a real estate baron starts here.</p></div>
    </div>
    <div class="action" style="left:620px">
      <div class="action-tile">
        <svg width="54" height="54" viewBox="0 0 54 54" aria-hidden="true"><circle cx="27" cy="27" r="24" fill="none" stroke="#fff" stroke-width="4"/><path d="M23 16 L34 27 L23 38" fill="none" stroke="#fff" stroke-width="4"/></svg>
        Submit a<br>property
      </div>
      <div><h3>Find buyer</h3><p>Submit a property or development and raise funds from our real estate barons.</p></div>
    </div>
  </section>

  <h2 class="section-title" style="top:1500px">Featured Projects</h2>
  <div class="section-rule" style="top:1553px"></div>
  <p class="section-lead" style="top:1562px">Brief details of new and popular projects. To view full listings, you will be required to<br><strong>sign up</strong> and <strong>become a member</strong></p>

  <article class="project" style="left:93px">
    <div class="project-photo" role="img" aria-label="Photo of a riverside apartment building at dusk"><span class="project-badge">new launch</span><span class="project-price">From GBP 3,600</span></div>
    <div class="project-body">
      <div class="project-name">14 Harbour Row, LONDON E1</div>
      <p class="project-desc">A landmark development in 21 differing panoramic views across the river, less than 2 miles from the City and the Docklands.</p>
      <div class="project-bar"><span style="width:0"></span></div>
      <div class="project-funded">0% funded</div>
      <div class="project-link">See Project Details</div>
    </div>
  </article>
  <article class="project" style="left:436px">
    <div class="project-photo" role="img" aria-label="Photo of a residential tower lit at night"><span class="project-badge">new launch</span><span class="project-price">From GBP 3,275</span></div>
    <div class="project-body">
      <div class="project-name">Meridian Tower, LONDON E14</div>
      <p class="project-desc">At the heart of Harbourline Wharf, a premium residential project by an award-winning developer, Kestrel Homes.</p>
      <div class="project-bar"><span style="width:4%"></span></div>
      <div class="project-funded">4% funded</div>
      <div class="project-link">See Project Details</div>
    </div>
  </article>
  <article class="project" style="left:779px">
    <div class="project-photo" role="img" aria-label="Photo of a new waterfront island development"><span class="project-price">From GBP 750</span></div>
    <div class="project-body">
      <div class="project-name">Riverside Quay Island E14</div>
      <p class="project-desc">A new island for London – introducing London's most connected location from the multi-award winning developer, Kestrel Homes.</p>
      <div class="project-bar"><span style="width:51%"></span></div>
      <div class="project-funded">51% funded</div>
      <div class="project-link">See Project Details</div>
    </div>
  </article>

  <h2 class="section-title" style="top:2050px">Be Part of a Growing International Community</h2>
  <p class="section-lead" style="top:2100px">Gain access to new projects in world class cities and join our growing community of<br>international landlords.</p>
  <div class="banner" style="top:2178px">A community of international property investors and real estate projects</div>
  <div class="world-map" role="img" aria-label="Dotted world map with green investor pins and pink property pins around the world"></div>
  <div class="legend" style="top:2760px"><i style="background:var(--green)"></i>A community of international property barons</div>
  <div class="legend" style="top:2806px"><i style="background:var(--pink)"></i>Attractive real estate from around the world</div>

  <div class="section-rule" style="top:2871px"></div>
  <div class="banner" style="top:2850px;left:320px;width:560px">Collective buying power of the pennyduke community</div>

  <svg class="donut" width="460" height="460" viewBox="0 0 460 460" role="img" aria-label="Donut chart: invested 15.8%, pledged 84.2%">
    <circle cx="230" cy="230" r="190" fill="none" stroke="var(--green)" stroke-width="60"/>
    <circle cx="230" cy="230" r="190" fill="none" stroke="var(--grey)" stroke-width="60"
      stroke-dasharray="188.6 1005" transform="rotate(-90 230 230)"/>
    <circle cx="230" cy="230" r="150" fill="var(--green)"/>
    <text x="230" y="215" text-anchor="middle" fill="#fff" font-family="Open Sans, sans-serif" font-size="40">* USD</text>
    <text x="230" y="280" text-anchor="middle" fill="#fff" font-family="Open Sans, sans-serif" font-size="62" font-weight="700">$2.06m</text>
  </svg>
  <svg style="position:absolute;top:2960px;left:700px" width="240" height="300" aria-hidden="true">
    <line x1="0" y1="20" x2="110" y2="20" stroke="#333" stroke-width="2"/>
    <line x1="60" y1="270" x2="110" y2="270" stroke="#333" stroke-width="2"/>
  </svg>
  <div class="donut-label" style="top:2966px;left:820px">Invested 15.8%</div>
  <div class="donut-label" style="top:3216px;left:820px">Pledged 84.2%</div>
  <p class="donut-note">* Graphic shows the combined USD$ amount invested in projects and pledged from aspiring pennydukes</p>

  <section class="press">
    <div class="press-label">Featured in</div>
    <div class="press-badge" style="left:120px;top:45px;width:120px"></div>
    <div class="press-badge" style="left:280px;top:50px;width:110px;height:30px"></div>
    <div class="press-badge" style="left:460px;top:45px;width:130px"></div>
    <div class="press-badge" style="left:660px;top:45px;width:80px"></div>
    <div class="press-badge" style="left:780px;top:45px;width:50px"></div>
    <div class="press-badge" style="left:860px;top:50px;width:130px;height:30px"></div>
    <div class="press-badge" style="left:120px;top:105px;width:60px"></div>
    <div class="press-badge" style="left:210px;top:105px;width:100px"></div>
    <div class="press-badge" style="left:330px;top:110px;width:320px;height:30px"></div>
  </section>

  <footer class="site-footer">
    <div class="footer-brand">risecapital group</div>
    <p class="lead">Penny Duke is part of the Rise Capital Group. The Rise Capital Group is a worldwide pioneer and leader in the crowd investing, peer to peer and online investment market.</p>
    <p>By accessing this site and any pages thereof, you agree to be bound by the terms and conditions. This website is only suitable and available for professional or sophisticated investors in certain jurisdictions, or those who are members of the community and familiar with and willing to accept the risks associated with private participation. Penny Duke does not endorse any of the projects that appear on this website, nor does it make any recommendations regarding the appropriateness of particular opportunities for any participant. Each potential participant must review and evaluate the projects in his or her own discretion.</p>
    <p>This website is in every respect unaffiliated with any site to which it links or to any company or entity mentioned. Furthermore, it is not meant as an endorsement of any of those companies or entities. If you believe your content has been reproduced on the Site without permission, please refer to our Terms of Service.</p>
  </footer>
  <div class="copyright">© pennyduke 2014 | Follow PennyDuke on <span class="circle"></span><span class="circle"></span></div>

</div>
</body>
</html>
```